RWT Fittings Ltd Business Cards

We need a business card with our business logo. We provide window and door installations on high-rises in west coast British Colombia, Canada.

I would like my business information and details on one side of the card, and the other side the company name with logo

Target Market(s)

General Contractors

Industry/Entity Type

Construction

Contact Information for Business Card

one side i want my company name and logo in the dark theme logo that i provided

Requirements
Must have
• Marco Peltieri, 16045518293, RWTFittings@mailbox-demo.com, 1407-5194 Linden Row Burnaby BC, V5H 2K9, Owner & Manager

```html
<!DOCTYPE html>
<html lang="en">
<head>
<meta charset="UTF-8">
<title>RWT Fittings Ltd – Business Card</title>
<link rel="stylesheet" href="https://fonts.googleapis.com/css2?family=Montserrat:wght@400;500;700&display=swap">
<style>
  :root {
    --page-bg: #d9dadc;
    --card-dark: #141416;
    --card-dark-edge: #2a2b2e;
    --card-light: #ffffff;
    --brand-blue: #2b9ad8;
    --brand-grey: #807b78;
    --ink: #2a2a2a;
    --ink-soft: #3d3d3d;
  }
  * { box-sizing: border-box; margin: 0; padding: 0; }
  html, body {
    width: 1200px; height: 808px; overflow: hidden;
    background: var(--page-bg);
    font-family: "Montserrat", Arial, sans-serif;
  }
  .canvas {
    width: 1200px; height: 808px;
    display: flex; flex-direction: column; align-items: center;
    justify-content: center; gap: 28px;
  }
  .card {
    width: 640px; height: 366px;
    position: relative; overflow: hidden;
    box-shadow: 0 10px 28px rgba(0,0,0,.22);
  }

  /* Front side */
  .card--front {
    background: radial-gradient(ellipse at 50% 30%, var(--card-dark-edge), var(--card-dark) 75%);
    display: flex; align-items: center; justify-content: center; gap: 22px;
  }
  .front-mark {
    width: 70px; height: 70px;
    background: var(--brand-grey);
  }
  .front-name {
    color: var(--brand-blue);
    font-weight: 700; font-size: 40px; letter-spacing: 1px;
    text-transform: uppercase; line-height: 1;
  }

  /* Back side */
  .card--back { background: var(--card-light); display: flex; }
  .back-feature {
    width: 260px; height: 100%; flex: none;
    background: linear-gradient(90deg, var(--brand-grey) 0%, var(--brand-grey) 45%, var(--card-light) 45%, var(--card-light) 50%, var(--brand-blue) 50%, var(--brand-blue) 82%, var(--card-light) 82%);
  }
  .back-info {
    flex: 1; min-width: 0;
    padding: 46px 22px 0 26px;
    color: var(--ink);
  }
  .back-brand {
    color: var(--brand-blue); font-weight: 700; font-size: 22px;
    text-transform: uppercase; letter-spacing: .5px; line-height: 1;
  }
  .holder-name {
    margin-top: 22px;
    color: var(--brand-blue); font-weight: 700; font-size: 27px; line-height: 1;
    text-transform: uppercase;
  }
  .holder-title {
    font-size: 18px; color: var(--ink-soft); margin-top: 4px;
  }
  .holder-rule {
    width: 90px; height: 2px; background: var(--brand-blue);
    margin: 8px 0 14px;
  }
  .contact-list { list-style: none; }
  .contact-item {
    display: flex; align-items: flex-start; gap: 10px;
    font-size: 16px; color: var(--ink); line-height: 1.45;
    margin-bottom: 4px;
  }
  .contact-icon { width: 17px; height: 17px; margin-top: 3px; fill: var(--ink-soft); flex: none; }
</style>
</head>
<body>
<main class="canvas">
  <section class="card card--front" aria-label="Card front">
    <span class="front-mark" aria-hidden="true"></span>
    <span class="front-name">RWT Fittings Ltd</span>
  </section>

  <section class="card card--back" aria-label="Card back">
    <div class="back-feature" role="img" aria-label="Large brand decoration in grey and blue"></div>
    <div class="back-info">
      <p class="back-brand">RWT Fittings Ltd</p>
      <h1 class="holder-name">Marco Peltieri</h1>
      <p class="holder-title">Owner &amp; Manager</p>
      <div class="holder-rule"></div>
      <ul class="contact-list">
        <li class="contact-item">
          <svg class="contact-icon" viewBox="0 0 24 24"><path d="M6.6 10.8a15 15 0 0 0 6.6 6.6l2.2-2.2a1 1 0 0 1 1-.25 11.4 11.4 0 0 0 3.6.57 1 1 0 0 1 1 1V20a1 1 0 0 1-1 1A17 17 0 0 1 3 4a1 1 0 0 1 1-1h3.5a1 1 0 0 1 1 1c0 1.25.2 2.45.57 3.57a1 1 0 0 1-.25 1z"/></svg>
          <span>16045518293</span>
        </li>
        <li class="contact-item">
          <svg class="contact-icon" viewBox="0 0 24 24"><path d="M2 5h20v14H2z M4 7v.3l8 5.2 8-5.2V7z" fill-rule="evenodd"/></svg>
          <span>RWTFittings@mailbox-demo.com</span>
        </li>
        <li class="contact-item">
          <svg class="contact-icon" viewBox="0 0 24 24"><path d="M12 2a7 7 0 0 0-7 7c0 5.2 7 13 7 13s7-7.8 7-13a7 7 0 0 0-7-7zm0 9.5a2.5 2.5 0 1 1 0-5 2.5 2.5 0 0 1 0 5z"/></svg>
          <span>1407-5194 Linden Row<br>Burnaby BC, V5H 2K9</span>
        </li>
      </ul>
    </div>
  </section>
</main>
</body>
</html>
```